Wordpress Website Update - Elementor

I'm currently using Elementor and would like my site to be updated. A nice facelift to the current pages. We are a small boutique animation service company.
I have a list of similar production houses to use as references and would like the format/style of the site not to feel so corporate and infuse the fun that we bring to working with clients on animated projects.

Additionally, I'd like to add 2 more pages focusing on more portfolio work and Original IP - which is now our primary goal to sell our show ideas. Maybe have a password projected behind an image showcasing the show/ film. Go to our current site to review. www.pebblemoatfilms.com

Animation/ Commercials/ Vorlica/ Quelbar/ Durno/ KVT - Okay with first page being shorter and not as long as well. Have contact us 'above the fold' on options as well.

Animation and Film

• Current 3 pages - additional 2 - we can focus on layout and arrangement with temporary images then swap with real assets when ready.
• site examples: pirtolstudios.com, Mardle House, Fenra Studios, Gorbleck.net, Quillstone Animation, Brindlemop Animation Studios, ZaZe Studios use Varkel Plus as inspiration.

```html
<!DOCTYPE html>
<html lang="en">
<head>
<meta charset="utf-8">
<title>Pebble Moat Films</title>
<link rel="stylesheet" href="https://fonts.googleapis.com/css2?family=Oswald:wght@600;700&family=Roboto:wght@400;500;700&display=swap">
<style>
:root{
  --purple:#6b3fe0;
  --purple-deep:#4f22c4;
  --violet:#7d5cf0;
  --red:#ea1750;
  --ink:#111111;
  --grey:#5c5c5c;
  --white:#ffffff;
  --black:#050505;
  --blue:#2a3ff0;
  --cyan:#1ed3ee;
}
*{margin:0;padding:0;box-sizing:border-box}
html,body{width:1200px;height:3013px;overflow:hidden}
body{position:relative;background:var(--white);font-family:'Roboto',sans-serif;color:var(--ink)}
.abs{position:absolute}

/* header */
.site-header{left:0;top:0;width:1200px;height:80px}
.brand{left:111px;top:25px;display:flex;align-items:center;gap:9px;font-weight:700;font-size:22px;color:var(--purple)}
.brand-mark{width:26px;height:26px;border-radius:50%;background:var(--purple)}
.main-nav{left:433px;top:30px;font-size:15px;font-weight:500}
.main-nav a{color:var(--ink);text-decoration:none;position:absolute;white-space:nowrap;top:0}
.social-dot{width:37px;height:37px;border-radius:50%;background:linear-gradient(135deg,var(--violet),var(--purple-deep));display:flex;align-items:center;justify-content:center}
.social-dot i{width:11px;height:11px;border-radius:50%;border:2px solid var(--white)}

/* hero strip */
.hero-tile{top:80px;height:603px}
.t1{left:0;width:290px;background:
  radial-gradient(ellipse 60% 30% at 30% 85%,#5fa7d8 0,rgba(95,167,216,0) 100%),
  linear-gradient(180deg,#d9b48a 0,#b7753f 28%,#7a4a26 45%,#5f8f3a 65%,#3d7a34 80%,#c2b49c 100%)}
.t2{left:301px;width:293px;background:
  radial-gradient(ellipse 45% 55% at 50% 45%,#b07a3d 0,#8a5a2c 55%,rgba(138,90,44,0) 75%),
  linear-gradient(180deg,#9a9aa0 0,#7e7f86 40%,#6d6a68 75%,#d6d2cc 100%)}
.t3{left:604px;width:293px;background:
  radial-gradient(ellipse 40% 30% at 65% 45%,#6d6fd8 0,rgba(109,111,216,0) 100%),
  linear-gradient(180deg,#2f1f6e 0,#3a3fb4 35%,#2c43c8 60%,#10207a 85%,#091552 100%)}
.t4{left:906px;width:294px;background:
  radial-gradient(ellipse 35% 40% at 50% 55%,#3c5d7e 0,rgba(60,93,126,0) 100%),
  linear-gradient(180deg,#5cc0f0 0,#2a8edc 35%,#1767c2 65%,#0a3a86 100%)}

/* feature rows */
.video{overflow:hidden}
.video.one{background:
  radial-gradient(ellipse 35% 45% at 50% 45%,#e7e2ee 0,#c9b6d8 40%,rgba(201,182,216,0) 75%),
  linear-gradient(135deg,#5a3bd0,#8e6ee6 45%,#2e1a7a)}
.video.two{background:
  radial-gradient(ellipse 30% 25% at 45% 45%,#9a5a2c 0,rgba(154,90,44,0) 100%),
  linear-gradient(180deg,#cfd2d8 0,#5a4a3c 18%,#3b3b3f 50%,#c9c6c0 82%,#ecebe8 100%)}
.play{left:50%;top:50%;width:58px;height:58px;margin:-29px 0 0 -29px}
.badge{width:61px;height:61px;border-radius:50%;background:linear-gradient(135deg,var(--blue),var(--violet));display:flex;align-items:center;justify-content:center}
.feature-title{font-family:'Oswald',sans-serif;font-weight:700;font-size:36px;line-height:43px;color:var(--purple);white-space:nowrap}
.feature-text{font-size:15px;line-height:21px;color:var(--grey)}
.btn{display:flex;align-items:center;justify-content:center;gap:10px;height:47px;border-radius:24px;background:var(--red);color:var(--white);font-weight:700;font-size:17px;text-transform:uppercase;text-decoration:none}

/* info cards */
.info-card{top:1673px;width:369px;height:305px;color:var(--white);text-align:center;background:
  radial-gradient(ellipse 50% 40% at 30% 30%,rgba(255,255,255,.08) 0,rgba(255,255,255,0) 100%),
  linear-gradient(160deg,var(--blue) 20%,#1a8be6 70%,var(--cyan))}
.info-card h3{position:absolute;left:0;right:0;top:94px;font-family:'Oswald',sans-serif;font-weight:600;font-size:26px;line-height:34px}
.info-card .rule{position:absolute;left:50%;top:134px;width:54px;height:4px;margin-left:-27px;background:var(--white)}
.info-card p{position:absolute;left:0;right:0;top:162px;font-size:16px;line-height:27px}
.card-icons{position:absolute;left:0;right:0;top:184px;display:flex;justify-content:center;gap:16px}
.card-icons span{width:15px;height:15px;border-radius:3px;border:2px solid var(--white)}

/* expertise */
.expertise{left:0;top:2004px;width:1200px;height:665px;background:linear-gradient(135deg,#8a6cf0,#6a45e2 50%,#5020c2)}
.expertise h2{position:absolute;left:0;right:0;top:57px;text-align:center;font-family:'Oswald',sans-serif;font-weight:700;font-size:38px;line-height:46px;color:var(--white)}
.skill{width:300px;color:var(--white)}
.skill h4{font-size:19px;line-height:22px;font-weight:700;text-transform:uppercase;margin-bottom:10px}
.skill p{font-size:13px;line-height:20px}
.skill.left{text-align:right}
.skill-icon{width:76px;height:76px;border-radius:50%;background:var(--white);display:flex;align-items:center;justify-content:center}
.mascot{left:468px;top:166px;width:256px;height:404px;background:
  radial-gradient(ellipse 50% 8% at 50% 97%,rgba(90,50,200,.35) 0,rgba(90,50,200,0) 100%),
  radial-gradient(ellipse 42% 48% at 50% 48%,#b79cff 0,#9572f4 55%,#8458ea 80%,rgba(132,88,234,0) 100%),
  radial-gradient(ellipse 14% 22% at 52% 12%,#d9a8f5 0,rgba(217,168,245,0) 100%)}

/* footer */
.site-footer{left:0;top:2669px;width:1200px;height:344px;background:var(--black);color:var(--white);text-align:center}
.footer-brand{position:absolute;left:0;right:0;top:86px;display:flex;justify-content:center;align-items:center;gap:10px;font-weight:700;font-size:30px;color:var(--violet)}
.footer-brand i{width:30px;height:30px;border-radius:50%;background:var(--violet)}
.footer-nav{position:absolute;left:0;right:0;top:161px;display:flex;justify-content:center;gap:29px;font-size:14px;font-weight:700}
.copyright{position:absolute;left:0;right:0;top:199px;font-size:14px}
.copyright u{text-underline-offset:2px}
.footer-social{position:absolute;left:501px;top:248px;display:flex;gap:7px}
.footer-social span{width:44px;height:44px;border-radius:50%;background:#e8e8e8;display:flex;align-items:center;justify-content:center}
.footer-social span i{width:13px;height:13px;border-radius:50%;border:2px solid #222}
.footer-social span:first-child{background:linear-gradient(135deg,var(--violet),var(--purple-deep))}
.footer-social span:first-child i{border-color:var(--white)}
</style>
</head>
<body>

<header class="site-header abs">
  <div class="brand abs"><span class="brand-mark"></span>Pebble Moat Films</div>
  <nav class="main-nav abs">
    <a style="left:0">Home</a>
    <a style="left:72px">About Us</a>
    <a style="left:166px">Team</a>
    <a style="left:235px">Projects</a>
    <a style="left:323px">Careers</a>
    <a style="left:407px">Contact Us</a>
  </nav>
  <span class="social-dot abs" style="left:963px;top:21px" aria-label="Social link"><i></i></span>
  <span class="social-dot abs" style="left:1007px;top:21px" aria-label="Social link"><i></i></span>
  <span class="social-dot abs" style="left:1050px;top:21px" aria-label="Social link"><i></i></span>
</header>

<div class="hero-tile t1 abs" role="img" aria-label="Painted forest scene with cartoon characters by a stream"></div>
<div class="hero-tile t2 abs" role="img" aria-label="Animated giraffe wearing glasses"></div>
<div class="hero-tile t3 abs" role="img" aria-label="Blue night scene of a sailing boat before a domed palace"></div>
<div class="hero-tile t4 abs" role="img" aria-label="Underwater scene of a diving bear among fish"></div>

<div class="video one abs" style="left:111px;top:795px;width:489px;height:320px" role="img" aria-label="Animation reel video still with a puppy character">
  <svg class="play abs" viewBox="0 0 58 58"><circle cx="29" cy="29" r="29" fill="rgba(20,10,40,.6)"/><polygon points="23,18 23,40 41,29" fill="#fff"/></svg>
</div>
<div class="badge abs" style="left:668px;top:838px" aria-label="Animation reel icon">
  <svg width="30" height="30" viewBox="0 0 30 30" fill="none" stroke="#fff" stroke-width="2"><rect x="3" y="5" width="24" height="16" rx="2"/><path d="M11 26h8M15 21v5"/><polygon points="13,9 13,17 19,13" fill="#fff" stroke="none"/></svg>
</div>
<h2 class="feature-title abs" style="left:668px;top:902px">ANIMATION REEL</h2>
<p class="feature-text abs" style="left:668px;top:968px">Story and Animation is where PMF thrives.</p>
<a class="btn abs" style="left:668px;top:1026px;width:195px">Learn More
  <svg width="16" height="16" viewBox="0 0 16 16"><circle cx="8" cy="8" r="8" fill="#fff"/><path d="M6.5 4.5 10 8l-3.5 3.5" stroke="#ea1750" stroke-width="2" fill="none"/></svg></a>

<div class="badge abs" style="left:111px;top:1261px" aria-label="Commercial project icon">
  <svg width="30" height="30" viewBox="0 0 30 30" fill="none" stroke="#fff" stroke-width="2"><rect x="4" y="11" width="22" height="15" rx="1"/><path d="M4 11l20-6 1 4"/><path d="M10 9l3 3M16 7l3 3"/></svg>
</div>
<h2 class="feature-title abs" style="left:111px;top:1342px">GIRAFFES &amp; KIDS ARE FREE!</h2>
<p class="feature-text abs" style="left:111px;top:1407px;width:440px">Pebble Moat kicked major butt on this fun project. Read more about the role we played bringing this commercial to life...</p>
<a class="btn abs" style="left:111px;top:1476px;width:195px">Learn More
  <svg width="16" height="16" viewBox="0 0 16 16"><circle cx="8" cy="8" r="8" fill="#fff"/><path d="M6.5 4.5 10 8l-3.5 3.5" stroke="#ea1750" stroke-width="2" fill="none"/></svg></a>
<div class="video two abs" style="left:600px;top:1232px;width:488px;height:320px" role="img" aria-label="Commercial video still with a giraffe beside a painting of an ark">
  <svg class="play abs" viewBox="0 0 58 58"><circle cx="29" cy="29" r="29" fill="rgba(20,10,40,.6)"/><polygon points="23,18 23,40 41,29" fill="#fff"/></svg>
</div>

<section class="info-card abs" style="left:23px">
  <h3>CONTACT</h3><span class="rule"></span>
  <p>hello@pebblemoatfilms.com<br>+1 (555) 010-0142</p>
</section>
<section class="info-card abs" style="left:415px">
  <h3>VISIT</h3><span class="rule"></span>
  <p>123, Lorem ipsum dolor sit amet,<br>consectetur adipiscing elit,</p>
</section>
<section class="info-card abs" style="left:807px">
  <h3 style="top:108px">SOCIALIZE</h3><span class="rule" style="top:148px"></span>
  <div class="card-icons"><span></span><span></span><span></span><span></span><span></span></div>
</section>

<section class="expertise abs">
  <h2>OUR EXPERTISE</h2>
  <div class="mascot abs" role="img" aria-label="Furry purple one-eyed monster mascot"></div>

  <div class="skill left abs" style="left:25px;top:168px"><h4>IP Creation</h4><p>Developing, Directing and Selling captivating stories is in our DNA. Check what we are cooking up.</p></div>
  <div class="skill left abs" style="left:25px;top:318px"><h4>Story</h4><p>From Storyboarding, to Story Consulting, and Script Doctoring, PM turns your stories into attention making monsters!</p></div>
  <div class="skill left abs" style="left:25px;top:468px"><h4>Animation</h4><p>Pound for Pound we have worlds best animators and pride ourselves on the quality level we deliver.</p></div>

  <div class="skill-icon abs" style="left:352px;top:178px" aria-label="IP creation icon">
    <svg width="40" height="40" viewBox="0 0 40 40" fill="none" stroke="#5a3ad8" stroke-width="2"><path d="M20 6a10 10 0 0 0-6 18v4h12v-4a10 10 0 0 0-6-18z"/><path d="M15 32h10M17 35h6"/></svg></div>
  <div class="skill-icon abs" style="left:352px;top:329px" aria-label="Story icon">
    <svg width="42" height="40" viewBox="0 0 42 40" fill="none" stroke="#5a3ad8" stroke-width="2"><rect x="4" y="8" width="10" height="9"/><rect x="16" y="8" width="10" height="9"/><rect x="28" y="8" width="10" height="9"/><rect x="4" y="22" width="10" height="9"/><rect x="16" y="22" width="10" height="9"/><rect x="28" y="22" width="10" height="9"/></svg></div>
  <div class="skill-icon abs" style="left:352px;top:478px" aria-label="Animation icon">
    <svg width="40" height="40" viewBox="0 0 40 40" fill="none" stroke="#5a3ad8" stroke-width="2"><path d="M8 30l3-9 16-16 6 6-16 16z"/><path d="M11 21l6 6M24 8l6 6"/></svg></div>

  <div class="skill-icon abs" style="left:756px;top:178px" aria-label="3D rigging icon">
    <svg width="40" height="40" viewBox="0 0 40 40" fill="none" stroke="#5a3ad8" stroke-width="2"><circle cx="20" cy="9" r="3"/><circle cx="9" cy="20" r="3"/><circle cx="31" cy="20" r="3"/><circle cx="20" cy="31" r="3"/><path d="M20 12v16M12 20h16"/></svg></div>
  <div class="skill-icon abs" style="left:756px;top:329px" aria-label="Character design icon">
    <svg width="40" height="40" viewBox="0 0 40 40" fill="none" stroke="#5a3ad8" stroke-width="2"><rect x="6" y="8" width="28" height="22" rx="2"/><path d="M14 26l14-12 3 3-14 12h-3z"/></svg></div>
  <div class="skill-icon abs" style="left:756px;top:478px" aria-label="Visual development icon">
    <svg width="40" height="40" viewBox="0 0 40 40" fill="none" stroke="#5a3ad8" stroke-width="2"><rect x="5" y="8" width="30" height="24" rx="2"/><path d="M5 28l9-9 7 7 5-5 9 9"/><circle cx="27" cy="15" r="2.5"/></svg></div>

  <div class="skill abs" style="left:857px;top:174px;width:270px"><h4>3D Rigging</h4><p>Creating Feature level robust rigs to game and real time rigs with dynamics.</p></div>
  <div class="skill abs" style="left:857px;top:327px;width:270px"><h4>Character Design</h4><p>Designing premier characters from concept to finished packets for 3D Development.</p></div>
  <div class="skill abs" style="left:857px;top:468px;width:270px"><h4>Vis Dev</h4><p>Building worlds and settings to enrich the places characters play. Saying more with an image.</p></div>
</section>

<footer class="site-footer abs">
  <div class="footer-brand"><i></i>Pebble Moat Films</div>
  <nav class="footer-nav">
    <span>HOME</span><span>/</span><span>ABOUT US</span><span>/</span><span>TEAM</span><span>/</span><span>PROJECTS</span><span>/</span><span>CAREERS</span><span>/</span><span>CONTACT US</span>
  </nav>
  <p class="copyright">Copyright© 2022 <u>pebblemoatfilms</u> &nbsp;|&nbsp; All Rights Reserved</p>
  <div class="footer-social"><span><i></i></span><span><i></i></span><span><i></i></span><span><i></i></span></div>
</footer>

</body>
</html>
```